MRT Property - Business Cards

Looking for a business card & general letterhead, signage etc design for our new logo.

Colours:
000a20
0056a2
00b5ef
0088ce
68cef2

Fonts:
Poppins
Karla

Please keep look and feel of new brand - example in the zip package I sent.

```html
<!DOCTYPE html>
<html lang="en">
<head>
<meta charset="utf-8">
<title>MRT Property – Business Cards</title>
<link rel="stylesheet" href="https://fonts.googleapis.com/css2?family=Poppins:wght@400;500;600&display=swap">
<style>
  :root {
    --backdrop: #222222;
    --card-navy: #0f1428;
    --ink-white: #ffffff;
    --brand-deep: #0056a2;
    --brand-mid: #0088ce;
    --brand-cyan: #00b5ef;
    --brand-sky: #68cef2;
  }
  * { margin: 0; padding: 0; box-sizing: border-box; }
  html, body {
    width: 1200px; height: 780px; overflow: hidden;
    background: var(--backdrop);
    font-family: "Poppins", sans-serif;
  }
  .stage {
    position: relative; width: 1200px; height: 780px;
    display: flex; align-items: center; justify-content: center; gap: 40px;
  }
  .card {
    position: relative; width: 540px; height: 310px;
    background: var(--card-navy);
    overflow: hidden;
    box-shadow: 0 12px 30px rgba(0,0,0,.45);
  }
  .wordmark {
    display: flex; align-items: center; gap: 10px;
    color: var(--ink-white); font-weight: 600; letter-spacing: .5px;
  }
  .wordmark-square { background: var(--brand-sky); flex: none; }

  /* front */
  .card-front .wordmark { position: absolute; left: 36px; top: 34px; font-size: 28px; }
  .card-front .wordmark-square { width: 18px; height: 18px; }
  .contact-list {
    position: absolute; left: 36px; top: 112px; list-style: none;
    color: var(--ink-white); font-size: 11px; line-height: 20px;
  }
  .contact-list li { display: flex; align-items: center; gap: 8px; }
  .contact-list svg { width: 11px; height: 11px; flex: none; }
  .person {
    position: absolute; right: 30px; top: 78px; text-align: right;
  }
  .person-name { font-size: 27px; font-weight: 500; line-height: 1.1; }
  .person-first { color: var(--brand-deep); font-weight: 600; }
  .person-last { color: var(--brand-sky); }
  .person-role { color: var(--ink-white); font-size: 13px; }
  .edge-tab {
    position: absolute; right: 0; top: 96px; width: 10px; height: 46px;
    background: var(--brand-sky);
  }
  .address {
    position: absolute; right: 30px; top: 178px; text-align: right;
    color: var(--ink-white); font-size: 12px; line-height: 18px;
  }
  .wave-band { position: absolute; left: 0; bottom: 0; width: 540px; height: 310px; }

  /* back */
  .card-back .wordmark { position: absolute; right: 34px; bottom: 34px; font-size: 24px; }
  .card-back .wordmark-square { width: 15px; height: 15px; }
</style>
</head>
<body>
<main class="stage">
  <section class="card card-front" aria-label="Business card front">
    <svg class="wave-band" viewBox="0 0 540 310" aria-hidden="true">
      <path d="M0 200 Q 260 230 470 310 L0 310 Z" fill="var(--brand-sky)"/>
      <path d="M0 226 Q 250 246 452 310 L0 310 Z" fill="var(--card-navy)"/>
      <path d="M0 232 Q 250 252 440 310 L0 310 Z" fill="var(--brand-deep)"/>
    </svg>

    <div class="wordmark"><span class="wordmark-square"></span>MRT Property</div>

    <ul class="contact-list">
      <li>
        <svg viewBox="0 0 12 12"><path d="M3 1 L5 3.5 L4 5 Q5 7 7 8 L8.5 7 L11 9 L9.5 11 Q4 10.5 1 2.5 Z" fill="var(--brand-cyan)"/></svg>
        +61 2 9555 0142
      </li>
      <li>
        <svg viewBox="0 0 12 12"><circle cx="6" cy="6" r="5" fill="none" stroke="var(--brand-cyan)" stroke-width="1.3"/><path d="M1 6 H11 M6 1 Q3 6 6 11 M6 1 Q9 6 6 11" fill="none" stroke="var(--brand-cyan)" stroke-width="1"/></svg>
        www.mrtproperty.com.au
      </li>
      <li>
        <svg viewBox="0 0 12 12"><rect x="1" y="2.5" width="10" height="7" fill="none" stroke="var(--brand-cyan)" stroke-width="1.3"/><path d="M1 2.5 L6 6.5 L11 2.5" fill="none" stroke="var(--brand-cyan)" stroke-width="1.2"/></svg>
        info@mrtproperty.com.au
      </li>
    </ul>

    <div class="person">
      <p class="person-name"><span class="person-first">Ellis</span> <span class="person-last">Harper</span></p>
      <p class="person-role">Director</p>
    </div>
    <div class="edge-tab"></div>

    <address class="address" style="font-style:normal">
      Suite 4.12, Level 4<br>
      18 Harbourline Road<br>
      Riverside Park NSW 2199
    </address>
  </section>

  <section class="card card-back" aria-label="Business card back">
    <div class="wordmark"><span class="wordmark-square"></span>MRT Property</div>
  </section>
</main>
</body>
</html>
```